Business card for my new company (Accounting firm)

I need a business card for my new business Brightwell Advisory and Ledger SA. Our services are accounting, tax, audit and financial management. Our customers are small companies, start-ups and new companies. The final design has to show financial security, trust and growth. Please find our logo attached to the business card. Text for the business card: Brightwell Advisory and Ledger SA Tomas Varenholt Director and Founder Certified Accountant Tel. 022 418 57 34 tv@clairevalconseil.ch www.clairevalconseil.ch Rue des Vergières 27 1201 Geneva
Target Market(s)
Our customers are small companies, start-ups and new companies.
Industry/Entity Type
Finance And Accounting
Contact Information for Business Card
Claireval Conseil et Comptes SA
Tomas Varenholt
Directeur et Fondateur
Expert-comptable diplômé
Tél. 022 418 57 34
tv@clairevalconseil.ch
www.clairevalconseil.ch
Rue des Vergières 27
1201 Genève

```html
<!DOCTYPE html>
<html lang="en">
<head>
<meta charset="utf-8">
<title>Claireval Conseil et Comptes SA – Business Card</title>
<link rel="stylesheet" href="https://fonts.googleapis.com/css2?family=Lato:wght@400;700&display=swap">
<style>
  :root {
    --backdrop: #8a5a36;
    --kraft-light: #dcbf95;
    --kraft-mid: #c29a6c;
    --kraft-dark: #a57650;
    --ink: #111111;
    --rule: #6b5138;
  }
  * { margin: 0; padding: 0; box-sizing: border-box; }
  html, body {
    width: 1200px;
    height: 900px;
    overflow: hidden;
    background: var(--backdrop);
  }
  .canvas {
    position: relative;
    width: 1200px;
    height: 900px;
    font-family: "Lato", sans-serif;
    color: var(--ink);
  }
  .card {
    position: absolute;
    left: 330px;
    width: 557px;
    height: 343px;
    background: radial-gradient(ellipse at 35% 20%, var(--kraft-light) 0%, var(--kraft-mid) 55%, var(--kraft-dark) 100%);
    box-shadow: 3px 4px 6px rgba(0,0,0,0.45);
  }
  .card--back { top: 90px; }
  .card--front { top: 469px; }

  .contact {
    position: absolute;
    inset: 0;
    text-align: center;
    padding-top: 60px;
  }
  .contact__name {
    font-weight: 700;
    font-size: 17px;
    letter-spacing: 0.2px;
    line-height: 24px;
  }
  .contact__role {
    font-size: 15px;
    line-height: 19px;
  }
  .contact__divider {
    display: flex;
    align-items: center;
    justify-content: center;
    margin: 9px auto 8px;
    width: 178px;
    gap: 3px;
  }
  .contact__divider::before,
  .contact__divider::after {
    content: "";
    flex: 1;
    height: 1px;
    background: var(--rule);
  }
  .contact__icon { width: 21px; height: 21px; display: block; }
  .contact__line {
    font-size: 15px;
    line-height: 20px;
  }
  .contact__rule {
    width: 178px;
    height: 1px;
    background: var(--rule);
    margin: 8px auto 9px;
  }

  .brand {
    position: absolute;
    inset: 0;
    display: flex;
    flex-direction: column;
    align-items: center;
    justify-content: center;
    padding-top: 40px;
  }
  .brand__mark {
    width: 26px;
    height: 26px;
    border-radius: 50%;
    background: var(--ink);
    margin-bottom: 18px;
  }
  .brand__name {
    font-weight: 700;
    font-size: 40px;
    letter-spacing: 3px;
    line-height: 44px;
  }
  .brand__tagline {
    font-weight: 700;
    font-size: 13px;
    letter-spacing: 2px;
    margin-top: 4px;
  }
</style>
</head>
<body>
<main class="canvas">
  <section class="card card--back">
    <div class="contact">
      <p class="contact__name">SA TOMAS VARENHOLT</p>
      <p class="contact__role">Director and Founder</p>
      <p class="contact__role">Certified Accountant</p>
      <div class="contact__divider">
        <svg class="contact__icon" viewBox="0 0 24 24" aria-label="Phone">
          <circle cx="12" cy="12" r="12" fill="#111"/>
          <path d="M6 10c0-2 2-3 6-3s6 1 6 3l-2 1-1-2h-6l-1 2z M8 12h8l1 5H7z" fill="#c9a477"/>
        </svg>
        <svg class="contact__icon" viewBox="0 0 24 24" aria-label="Email">
          <circle cx="12" cy="12" r="12" fill="#111"/>
          <rect x="6" y="8" width="12" height="8" fill="#c9a477"/>
          <path d="M6 8l6 5 6-5" fill="none" stroke="#111" stroke-width="1.2"/>
        </svg>
        <svg class="contact__icon" viewBox="0 0 24 24" aria-label="Website">
          <circle cx="12" cy="12" r="12" fill="#111"/>
          <circle cx="12" cy="12" r="6" fill="#c9a477"/>
          <path d="M6 12h12 M12 6c-3 3-3 9 0 12 M12 6c3 3 3 9 0 12" fill="none" stroke="#111" stroke-width="1"/>
        </svg>
      </div>
      <p class="contact__line">022 418 57 34</p>
      <p class="contact__line">tv@clairevalconseil.ch</p>
      <p class="contact__line">www.clairevalconseil.ch</p>
      <div class="contact__rule"></div>
      <p class="contact__line">Rue des Vergières 27</p>
      <p class="contact__line">1201 Geneva</p>
    </div>
  </section>

  <section class="card card--front">
    <div class="brand">
      <span class="brand__mark"></span>
      <p class="brand__name">CLAIREVAL</p>
      <p class="brand__tagline">CONSEIL ET COMPTES</p>
    </div>
  </section>
</main>
</body>
</html>
```